Family Values Statement Image

I have created a statement of values for my family. Our last name is Pilwothy, and we are using those letters as an acronym. I would like an image with these words and letters with a tree with deep roots, where the roots are the focal point.

A - All In
N - Never Settle
D - Dependable
E - Enthusiastic
R - Repair
E - Enduring
G - Gushy Hearted
G - Gratitudes

Note that "gratitudes" is intentionally misspelled.

• On further reflection, I am interested in the words being much more prominent than the tree. In fact, the tree could be quite small or even just a watermark behind the words.

```html
<!DOCTYPE html>
<html lang="en">
<head>
<meta charset="utf-8">
<title>Family Values – Pilwothy</title>
<link rel="stylesheet" href="https://fonts.googleapis.com/css2?family=Cinzel:wght@600;700&family=Montserrat:wght@600&family=Great+Vibes&display=swap">
<style>
  :root {
    --bg: #0b0b0b;
    --ink-light: #f2f2f2;
    --ink-mid: #b9b6b2;
    --icon: #cfcfcf;
    --script: #5a5a5a;
    --tree-soft: #1c1c1c;
    --tree-top: #8a8a8a;
    --tree-top-deep: #3e3e3e;
  }
  html, body {
    margin: 0;
    padding: 0;
    width: 1122px;
    height: 1200px;
    overflow: hidden;
    background: var(--bg);
  }
  .poster {
    position: relative;
    width: 1122px;
    height: 1200px;
    background: var(--bg);
    overflow: hidden;
  }
  .watermark-tree {
    position: absolute;
    right: -80px;
    bottom: -60px;
    width: 640px;
    height: 860px;
    background: radial-gradient(closest-side at 50% 50%, var(--tree-soft) 0%, rgba(28,28,28,0.55) 55%, rgba(11,11,11,0) 100%);
  }
  .badge-tree {
    position: absolute;
    top: 60px;
    right: 80px;
    width: 220px;
    height: 190px;
    background: radial-gradient(closest-side at 50% 45%, var(--tree-top) 0%, var(--tree-top-deep) 60%, rgba(11,11,11,0) 100%);
  }
  .header {
    position: absolute;
    top: 70px;
    left: 80px;
    width: 560px;
    height: 160px;
  }
  .header-title {
    position: absolute;
    left: 150px;
    top: 0;
    margin: 0;
    font-family: "Montserrat", sans-serif;
    font-weight: 600;
    font-size: 36px;
    line-height: 1.2;
    letter-spacing: 0.5px;
    color: var(--ink-light);
  }
  .family-name {
    position: absolute;
    left: 0;
    top: 62px;
    font-family: "Great Vibes", cursive;
    font-size: 80px;
    color: var(--script);
    line-height: 1;
  }
  .values {
    position: absolute;
    top: 262px;
    left: 70px;
    margin: 0;
    padding: 0;
    list-style: none;
  }
  .value {
    display: flex;
    align-items: center;
    height: 104px;
  }
  .value-icon {
    width: 84px;
    height: 74px;
    margin-right: 30px;
    flex: none;
  }
  .value-icon svg {
    width: 100%;
    height: 100%;
    fill: var(--icon);
  }
  .value-word {
    font-family: "Cinzel", serif;
    font-weight: 700;
    font-size: 78px;
    line-height: 1;
    background: linear-gradient(90deg, var(--ink-light) 0%, var(--ink-light) 40%, var(--ink-mid) 100%);
    -webkit-background-clip: text;
    background-clip: text;
    color: transparent;
  }
</style>
</head>
<body>
<main class="poster">
  <div class="watermark-tree" role="img" aria-label="Faint silhouette of a large tree with spreading roots"></div>
  <div class="badge-tree" role="img" aria-label="Small tree emblem with leafy crown and roots"></div>

  <header class="header">
    <h1 class="header-title">FAMILY VALUES</h1>
    <span class="family-name">Pilwothy</span>
  </header>

  <ul class="values">
    <li class="value">
      <span class="value-icon"><svg viewBox="0 0 84 74"><path d="M12 38 l10 -10 l12 14 l30 -34 l10 9 l-40 46 z"/></svg></span>
      <span class="value-word">All In</span>
    </li>
    <li class="value">
      <span class="value-icon"><svg viewBox="0 0 84 74"><path d="M22 22 c-9 0 -16 7 -16 15 s7 15 16 15 c8 0 13 -6 20 -15 c7 -9 12 -15 20 -15 c9 0 16 7 16 15 s-7 15 -16 15 c-8 0 -13 -6 -20 -15 c-7 -9 -12 -15 -20 -15 z" fill="none" stroke="#cfcfcf" stroke-width="7"/></svg></span>
      <span class="value-word">Never Settle</span>
    </li>
    <li class="value">
      <span class="value-icon"><svg viewBox="0 0 84 74"><path d="M4 22 l14 -12 l14 10 l14 -4 l20 18 l-10 10 l-16 -14 l-10 4 l18 18 l-6 6 l-6 -6 l-6 6 l-6 -6 l-6 6 z"/><path d="M58 10 l20 14 l-8 10 l-18 -16 z"/></svg></span>
      <span class="value-word">Dependable</span>
    </li>
    <li class="value">
      <span class="value-icon"><svg viewBox="0 0 84 74"><circle cx="42" cy="14" r="9"/><path d="M4 8 l10 -4 l16 26 h24 l16 -26 l10 4 l-18 32 v32 h-40 v-32 z"/></svg></span>
      <span class="value-word">Enthusiastic</span>
    </li>
    <li class="value">
      <span class="value-icon"><svg viewBox="0 0 84 74"><path d="M58 4 a16 16 0 0 0 -14 22 l-32 32 a6 6 0 0 0 9 9 l32 -32 a16 16 0 0 0 22 -14 l-8 7 l-9 -3 l-3 -9 z"/></svg></span>
      <span class="value-word">Repair</span>
    </li>
    <li class="value">
      <span class="value-icon"><svg viewBox="0 0 84 74"><path d="M34 14 a8 8 0 1 1 16 0 v4 h10 l14 52 h-64 l14 -52 h10 z M39 14 v4 h6 v-4 a3 3 0 0 0 -6 0 z"/></svg></span>
      <span class="value-word">Enduring</span>
    </li>
    <li class="value">
      <span class="value-icon"><svg viewBox="0 0 84 74"><path d="M42 70 l-30 -30 a16 16 0 0 1 30 -24 a16 16 0 0 1 30 24 z"/></svg></span>
      <span class="value-word">Gushy Hearted</span>
    </li>
    <li class="value">
      <span class="value-icon"><svg viewBox="0 0 84 74"><path d="M42 38 l-12 -12 a7 7 0 0 1 12 -9 a7 7 0 0 1 12 9 z"/><path d="M6 50 h16 l12 -6 h18 a4 4 0 0 1 0 8 h-14 h16 l18 -10 a4 4 0 0 1 5 6 l-20 16 h-34 l-10 4 h-7 z"/></svg></span>
      <span class="value-word">Gradtitudes</span>
    </li>
  </ul>
</main>
</body>
</html>
```